Birchpoint Studio Complementary Pass

I’d like a complimentary pass for any 30-minute Birchpoint Studio session. Choose one of the following options: Infrared Sauna with Red Light, Massage Chair Veltrafix Compression Therapy, or Paraffin Wax Hand Bath.

Please incorporate the logo and brand colors into your design. I’d like a square image that will be printed on square business cards (no rectangles).

Please refer to the logo and menu for more details.

Contact Information for Business Card

See discretion

```html
<!DOCTYPE html>
<html lang="en">
<head>
<meta charset="utf-8">
<title>Birchpoint Studio – Complimentary Pass Cards</title>
<link rel="stylesheet" href="https://fonts.googleapis.com/css2?family=Yellowtail&family=Libre+Baskerville:ital,wght@0,400;0,700;1,400&family=Montserrat:wght@600;700&family=Open+Sans:wght@400;600&display=swap">
<style>
  :root {
    --stage: #232323;
    --card: #ffffff;
    --orange: #ef6a47;
    --purple: #45309a;
  }
  * { box-sizing: border-box; margin: 0; padding: 0; }
  html, body { width: 1200px; height: 800px; overflow: hidden; background: var(--stage); }
  .stage { position: relative; width: 1200px; height: 800px; }

  .card {
    position: absolute; top: 140px; width: 520px; height: 520px;
    background: var(--card); border-radius: 40px; overflow: hidden;
  }
  .card--front { left: 50px; }
  .card--back { left: 630px; }
  .card__frame {
    position: absolute; inset: 14px; border: 1.5px solid var(--orange); border-radius: 30px;
  }

  /* Brand wordmark */
  .brand { display: flex; align-items: center; gap: 14px; color: var(--purple); font-family: "Montserrat", sans-serif; font-weight: 700; }
  .brand__dot { background: var(--orange); border-radius: 50%; flex: none; }
  .brand__name { line-height: 1; letter-spacing: 0.5px; }
  .brand__sub { display: block; letter-spacing: 3px; }

  .card--front .brand { position: absolute; left: 0; right: 0; top: 200px; justify-content: center; }
  .card--front .brand__dot { width: 58px; height: 58px; }
  .card--front .brand__name { font-size: 40px; }
  .card--front .brand__sub { font-size: 15px; margin-top: 8px; }

  .card--back .brand { position: absolute; left: 0; right: 0; top: 42px; justify-content: center; gap: 10px; }
  .card--back .brand__dot { width: 30px; height: 30px; }
  .card--back .brand__name { font-size: 21px; }
  .card--back .brand__sub { font-size: 8px; margin-top: 4px; letter-spacing: 2px; }

  /* Pass content */
  .pass__title {
    position: absolute; left: 40px; right: 40px; top: 92px; text-align: center; white-space: nowrap;
    font-family: "Yellowtail", cursive; font-weight: 400; font-size: 34px; line-height: 1.2; color: var(--purple);
  }
  .pass__kicker-row {
    position: absolute; left: 46px; right: 46px; top: 140px;
    display: flex; align-items: center; gap: 14px;
  }
  .pass__kicker-row::before, .pass__kicker-row::after {
    content: ""; flex: 1; height: 1.5px; background: var(--purple);
  }
  .pass__kicker {
    font-family: "Libre Baskerville", serif; font-weight: 700; font-size: 19px; color: var(--orange); white-space: nowrap;
  }
  .pass__offer {
    position: absolute; left: 40px; right: 40px; top: 178px; text-align: center; white-space: nowrap;
    font-family: "Libre Baskerville", serif; font-weight: 700; font-size: 15px; color: var(--orange);
  }
  .pass__options {
    position: absolute; left: 70px; top: 212px; list-style: none;
    font-family: "Libre Baskerville", serif; font-size: 14px; color: var(--purple); line-height: 1.65;
  }
  .pass__options li { display: flex; align-items: center; gap: 8px; }
  .pass__options li::before { content: ""; width: 7px; height: 7px; border-radius: 50%; background: var(--orange); }
  .pass__rule { position: absolute; height: 1.5px; background: var(--purple); left: 60px; right: 40px; top: 300px; }
  .pass__terms {
    position: absolute; right: 52px; top: 312px;
    font-family: "Libre Baskerville", serif; font-weight: 700; font-size: 13px; color: var(--purple); line-height: 1.45;
  }

  /* Contact block */
  .contact { position: absolute; left: 44px; right: 40px; top: 360px; font-family: "Open Sans", sans-serif; color: var(--purple); }
  .contact__name { font-family: "Montserrat", sans-serif; font-weight: 700; font-size: 24px; line-height: 1.2; color: var(--orange); }
  .contact__role { font-family: "Montserrat", sans-serif; font-weight: 600; font-size: 12px; margin: 2px 0 10px; }
  .contact__row { display: flex; justify-content: space-between; font-size: 10.5px; padding-bottom: 6px; }
  .contact__row--top { border-bottom: 1.5px solid var(--purple); margin-bottom: 6px; }
  .contact__item { display: flex; align-items: center; gap: 5px; }
  .contact__item svg { width: 11px; height: 11px; fill: none; stroke: var(--orange); stroke-width: 2; }
  .pass__note {
    position: absolute; left: 30px; right: 30px; bottom: 32px; text-align: center; white-space: nowrap;
    font-family: "Libre Baskerville", serif; font-style: italic; font-size: 10px; color: var(--orange);
  }
</style>
</head>
<body>
<main class="stage">

  <section class="card card--front" aria-label="Card front">
    <div class="card__frame"></div>
    <div class="brand">
      <span class="brand__dot"></span>
      <span class="brand__name">Larkmoor<span class="brand__sub">PHYSICAL THERAPY</span></span>
    </div>
  </section>

  <section class="card card--back" aria-label="Card back">
    <div class="card__frame"></div>
    <div class="brand">
      <span class="brand__dot"></span>
      <span class="brand__name">Larkmoor<span class="brand__sub">PHYSICAL THERAPY</span></span>
    </div>

    <h1 class="pass__title">Complimentary Recovery Pass</h1>
    <div class="pass__kicker-row"><p class="pass__kicker">A la carte</p></div>
    <p class="pass__offer">Any 30-Minute Birchpoint Studio Session.</p>
    <ul class="pass__options">
      <li>Infrared Sauna + Red Light</li>
      <li>Massage Chair Veltrafix Compression Therapy</li>
      <li>Paraffin Wax Hand Bath</li>
    </ul>
    <div class="pass__rule"></div>
    <p class="pass__terms">(One pass per guest.<br>By appointment only.)</p>

    <div class="contact">
      <p class="contact__name">Mira Holloway</p>
      <p class="contact__role">Managing Director</p>
      <div class="contact__row contact__row--top">
        <span class="contact__item">
          <svg viewBox="0 0 24 24"><path d="M5 3h4l2 5-3 2a11 11 0 0 0 6 6l2-3 5 2v4a2 2 0 0 1-2 2A17 17 0 0 1 3 5a2 2 0 0 1 2-2z"/></svg>
          +469-555-0148
        </span>
        <span class="contact__item">
          <svg viewBox="0 0 24 24"><rect x="3" y="5" width="18" height="14" rx="2"/><path d="M3 7l9 6 9-6"/></svg>
          info@website.com
        </span>
        <span class="contact__item">
          <svg viewBox="0 0 24 24"><circle cx="12" cy="12" r="9"/><path d="M3 12h18M12 3c3 3 3 15 0 18M12 3c-3 3-3 15 0 18"/></svg>
          www.website.com
        </span>
      </div>
      <div class="contact__row">
        <span class="contact__item">
          <svg viewBox="0 0 24 24"><path d="M12 22s7-7 7-12a7 7 0 0 0-14 0c0 5 7 12 7 12z"/><circle cx="12" cy="10" r="2.5"/></svg>
          Street, Apartment, City, State, Post Code, Country
        </span>
      </div>
    </div>

    <p class="pass__note">*For safety, a rest/cool-down period is required after 30 minutes in the sauna.</p>
  </section>

</main>
</body>
</html>
```